The book is called "Distance Racing Blueprints: An In-Depth Manual for Achieving Your Peak Race Day - Featuring Schedules, Counsel and Target-Reaching Pointers "

It is a 6" x 9" book with 205 pages. This is an advanced book for runners who have been running and trying to hit their marathon goals, but haven't been able to do so. This needs to portray a professional coaching image and high performing athlete.

I have running photos of myself running marathons if you thought that was the route to take, but I'm open to your creative influence.

```html
<!DOCTYPE html>
<html lang="en">
<head>
<meta charset="utf-8">
<title>Distance Racing Blueprints – Cover Wrap</title>
<link rel="stylesheet" href="https://fonts.googleapis.com/css2?family=Anton&family=Montserrat:wght@400;500;700;800&display=swap">
<style>
  :root {
    --page-bg: #8b8b8b;
    --brand-blue: #12a6d4;
    --navy: #0d3d6e;
    --white: #ffffff;
    --body-ink: #2a2a2a;
    --sky-top: #e3eef8;
    --sky-mid: #a9cbeb;
    --track-blue: #2f7fcf;
    --track-deep: #1d5fae;
  }
  * { box-sizing: border-box; margin: 0; padding: 0; }
  html, body { width: 1200px; height: 1200px; overflow: hidden; }
  body { background: var(--page-bg); position: relative; font-family: "Montserrat", sans-serif; }

  .cover-wrap {
    position: absolute; left: 45px; top: 196px;
    width: 1110px; height: 808px;
    overflow: hidden;
    box-shadow: 0 14px 30px rgba(0,0,0,.35);
  }

  .cover-photo {
    position: absolute; left: 284px; top: 0; width: 826px; height: 808px;
    background:
      radial-gradient(ellipse 60% 35% at 30% 22%, rgba(255,255,255,.85), rgba(255,255,255,0) 70%),
      linear-gradient(180deg, var(--sky-top) 0%, var(--sky-mid) 42%, var(--track-blue) 70%, var(--track-deep) 100%);
  }

  .back-panel {
    position: absolute; left: 0; top: 0; width: 284px; height: 808px;
    background: var(--brand-blue);
    padding: 34px 15px 0 34px;
  }
  .back-panel .back-title {
    font-family: "Anton", sans-serif; color: var(--white);
    font-size: 48px; line-height: 56px; text-align: center;
    text-transform: uppercase; letter-spacing: .5px;
    margin-left: -20px;
  }
  .blurb {
    font-size: 11.6px; line-height: 14.6px; text-align: justify;
    font-weight: 400;
  }
  .back-panel .blurb { color: var(--white); margin-top: 16px; }
  .back-panel .blurb + .blurb { margin-top: 14px; }

  .author-badge {
    position: absolute; left: 331px; top: 47px; width: 142px; height: 142px;
    border-radius: 50%; background: var(--brand-blue);
    box-shadow: 2px 4px 5px rgba(0,0,0,.35);
  }
  .back-author {
    position: absolute; left: 300px; top: 200px;
    font-weight: 800; font-size: 27px; color: var(--navy); letter-spacing: -.3px;
  }
  .back-copy {
    position: absolute; left: 302px; top: 250px; width: 208px;
    color: var(--body-ink);
  }

  .spine-title, .spine-author {
    position: absolute; writing-mode: vertical-rl; white-space: nowrap;
  }
  .spine-title {
    left: 541px; top: 34px;
    font-family: "Anton", sans-serif; font-size: 26px; color: var(--navy);
    letter-spacing: .3px;
  }
  .spine-author {
    left: 544px; top: 622px;
    font-weight: 800; font-size: 18px; color: var(--white);
  }

  .sticker { position: absolute; left: 630px; top: 27px; width: 172px; height: 172px; }
  .sticker-text {
    position: absolute; left: 656px; top: 66px; width: 120px;
    font-family: "Anton", sans-serif; color: var(--white);
    font-size: 16px; line-height: 19px; text-align: center; text-transform: uppercase;
    transform: rotate(-11deg);
  }

  .title-band {
    position: absolute; left: 540px; top: 406px; width: 570px; height: 88px;
    background: var(--brand-blue);
  }
  .front-title {
    position: absolute; left: 598px; top: 222px;
    font-family: "Anton", sans-serif; color: var(--navy);
    font-size: 78px; line-height: 90px; text-transform: uppercase;
  }
  .front-subtitle {
    position: absolute; left: 606px; top: 504px; width: 380px;
    font-weight: 800; font-size: 17.5px; line-height: 25px;
    color: var(--navy); text-transform: uppercase;
  }
  .front-author {
    position: absolute; left: 662px; top: 738px;
    font-weight: 800; font-size: 40px; color: var(--white);
  }
</style>
</head>
<body>
  <section class="cover-wrap" aria-label="Book cover wrap: Distance Racing Blueprints">
    <div class="cover-photo" role="img" aria-label="Photograph of a runner breaking a finish-line ribbon on a blue stadium track with the word finish painted on the lane"></div>

    <aside class="back-panel">
      <h2 class="back-title">Distance<br>Racing<br>Blueprints</h2>
      <p class="blurb">Lorem ipsum dolor sit amet, consectetur adipisicing elit, sed do eiusmod tempor incididunt ut labore et dolore magna aliqua. Ut enim ad minim veniam, quis nostrud exercitation ullamco laboris nisi ut aliquip ex ea commodo consequat. Duis aute irure dolor in reprehenderit in voluptate velit esse cillum dolore eu fugiat nulla pariatur. Excepteur sint occaecat cupidatat non proident, sunt in culpa qui officia deserunt mollit anim id est laborum. Sed ut perspiciatis unde omnis iste natus error sit voluptatem accusantium doloremque laudantium, totam rem aperiam, eaque ipsa quae ab illo inventore veritatis et quasi architecto beatae vitae dicta sunt explicabo. Nemo enim ipsam voluptatem quia voluptas sit aspernatur aut odit aut fugit, sed quia consequuntur magni dolores eos qui ratione voluptatem sequi nesciunt. Neque porro quisquam est, qui dolorem ipsum quia dolor sit amet, consectetur, adipisci velit, sed quia non numquam eius modi tempora incidunt ut labore et dolore magnam aliquam quaerat voluptatem.</p>
      <p class="blurb">Lorem ipsum dolor sit amet, consectetur adipisicing elit, sed do eiusmod tempor incididunt ut labore et dolore magna aliqua. Ut enim ad minim veniam, quis nostrud exercitation.</p>
    </aside>

    <div class="author-badge" aria-hidden="true"></div>
    <h3 class="back-author">AUTHOR NAME</h3>
    <p class="blurb back-copy">Lorem ipsum dolor sit amet, consectetur adipisicing elit, sed do eiusmod tempor incididunt ut labore et dolore magna aliqua. Ut enim ad minim veniam, quis nostrud exercitation ullamco laboris nisi ut aliquip ex ea commodo consequat. Duis aute irure dolor in reprehenderit in voluptate velit esse cillum dolore eu fugiat nulla pariatur. Excepteur sint occaecat cupidatat non proident, sunt in culpa qui officia deserunt mollit anim id est laborum. Sed ut perspiciatis unde omnis iste natus error sit voluptatem accusantium doloremque laudantium, totam rem aperiam, eaque ipsa quae ab illo inventore veritatis et quasi architecto beatae vitae dicta.</p>

    <div class="spine-title">DISTANCE RACING BLUEPRINTS</div>
    <div class="spine-author">AUTHOR NAME</div>

    <svg class="sticker" viewBox="0 0 172 172" aria-hidden="true">
      <path d="M86 4 A82 82 0 1 1 22 138 Q60 120 58 160 A82 82 0 0 1 86 4Z" fill="#12a6d4"/>
      <path d="M22 138 Q60 120 58 160 Q36 152 22 138Z" fill="#e9eef3"/>
    </svg>
    <p class="sticker-text">Featuring schedules, counsel and target-reaching pointers</p>

    <div class="title-band" aria-hidden="true"></div>
    <h1 class="front-title">Distance<br>Racing<br>Blueprints</h1>
    <p class="front-subtitle">An in-depth manual for achieving your peak race day</p>
    <p class="front-author">AUTHOR NAME</p>
  </section>
</body>
</html>
```